Designing a Chocolate Bar's Package

We are a chocolate manufacturing company located in Lebanon. We produce chocolate on a wholesale level, and we are planning a new line of production at the moment.
We intend to be make small chocolate bars (about 30g) similar to the "Varnou Classica" bar with several flavors. 2 flavors have been decided so far (Mint flavored dark chocolate and Plain dark chocolate).
The packaging material will be similar to varnou's package as well. It won't be a carton box. It'll be some sort of paper wrapping the entire bar. So I am looking for a design that has a unique and cool front and back look.
If only one design is to be prepared, please choose either the mint's flavor or the plain dark chocolate, and prepare the design accordingly.
Updates
Project Deadline Extended
Reason: I still have some time to begin the production. The new deadline,therefore, is the end of this month.
Target Market(s)
basically all chocolate lovers...
Industry/Entity Type
It Company
Requirements
Must have
- I will be uploading our logo. Please make sure to use it in the design.

```html
<!DOCTYPE html>
<html lang="en">
<head>
<meta charset="utf-8">
<title>Almira Chocolate Bar Wrappers</title>
<link rel="stylesheet" href="https://fonts.googleapis.com/css2?family=Cinzel:wght@400;600&family=Petit+Formal+Script&display=swap">
<style>
  :root {
    --paper: #ffffff;
    --page: #ffffff;
    --cocoa: #4a2416;
    --dark-panel: #2a1610;
    --mint: #6dbf4b;
    --tan: #b98550;
    --frame: #3a3a3a;
    --text-light: #ffffff;
    --text-dark: #2e1a12;
  }
  * { box-sizing: border-box; margin: 0; padding: 0; }
  html, body { width: 1200px; height: 692px; overflow: hidden; background: var(--page); }
  .canvas { position: relative; width: 1200px; height: 692px; }

  .wrapper {
    position: absolute; top: 49px; width: 268px; height: 602px;
    background: var(--paper); border: 1px solid var(--frame); overflow: hidden;
  }
  .wrapper--mint { left: 145px; }
  .wrapper--dark { left: 760px; }

  .brand {
    position: absolute; top: 62px; left: 0; width: 100%;
    display: flex; align-items: center; justify-content: center; gap: 8px;
  }
  .brand__name {
    font-family: "Cinzel", serif; font-weight: 600; font-size: 38px;
    color: var(--cocoa); letter-spacing: 1px;
  }
  .brand__dot { width: 18px; height: 18px; border-radius: 50%; background: var(--tan); }

  .story-panel { position: absolute; left: 0; top: 104px; width: 222px; height: 300px; }
  .story-panel svg { position: absolute; inset: 0; }
  .story {
    position: absolute; left: 22px; top: 40px; width: 186px; height: 228px; overflow: hidden;
    font-family: "Petit Formal Script", cursive; font-size: 8.2px; line-height 1; line-height: 12.1px;
    text-align: justify; color: var(--text-light);
  }
  .wrapper--dark .story { color: var(--text-light); }
  .story__initial { float: left; font-size: 30px; line-height: 26px; margin-right: 4px; }
  .weight {
    position: absolute; right: 8px; bottom: 12px;
    font-family: "Cinzel", serif; font-size: 10px; color: var(--text-light);
  }

  .year-badge {
    position: absolute; left: 55px; top: 382px; width: 106px; height: 41px;
    border-radius: 50%; background: var(--tan); border: 1.5px solid var(--paper);
    box-shadow: 0 0 0 1px var(--tan);
    display: flex; align-items: center; justify-content: center;
    font-family: "Cinzel", serif; font-size: 22px; color: var(--text-light);
  }

  .flavour {
    position: absolute; left: 45px; top: 436px;
    font-family: "Cinzel", serif; font-weight: 400; font-size: 19.5px; line-height: 24px;
    letter-spacing: 1px; color: var(--text-dark);
  }

  .product-photo { position: absolute; right: 0; bottom: 18px; width: 178px; height: 88px; border-radius: 4px; }
  .product-photo--mint { background: linear-gradient(160deg, #7cc84a 0%, #5fa83c 35%, #4a2a1c 60%, #2e1a12 100%); }
  .product-photo--dark { background: radial-gradient(ellipse at 60% 55%, #5a3522 0%, #3a2015 55%, #ffffff 100%); }
</style>
</head>
<body>
<main class="canvas">

  <section class="wrapper wrapper--mint" aria-label="Mint flavoured dark chocolate wrapper">
    <div class="brand"><span class="brand__name">Almira</span><span class="brand__dot"></span></div>

    <div class="story-panel">
      <svg width="222" height="300" viewBox="0 0 222 300" aria-hidden="true">
        <path d="M0 12 C60 0 120 18 222 4 L222 300 L0 300 Z" fill="var(--mint)"/>
      </svg>
      <p class="story"><span class="story__initial">L</span>orem ipsum dolor sit amet, siala conadipisicing elit, sed do nulla in eiusmod tempor incididunt ut labore et dolore magna aliqua. Ut enim ad minim veniam, quis nostrud exercitation ullamco laboris nisi ut aliquip ex ea commodo consequat. Duis aute irure dolor in reprehenderit in voluptate velit esse cillum dolore eu fugiat nulla pariatur. Excepteur sint occaecat cupidatat non proident, sunt in culpa qui officia deserunt mollit de aboriable seool animidest laborum prehenderit in voluptate velit esse cillum dolore eu fugiat nulla pariatur cillum dolore eu fugiat nulla pariatur cillum dolore.</p>
      <span class="weight">30g</span>
    </div>

    <div class="year-badge">1989</div>
    <h2 class="flavour">MINT FLAVOURED<br>DARK CHOCOLATE</h2>
    <div class="product-photo product-photo--mint" role="img" aria-label="Photo of mint leaves resting on dark chocolate squares"></div>
  </section>

  <section class="wrapper wrapper--dark" aria-label="Plain dark chocolate wrapper">
    <div class="brand"><span class="brand__name">Almira</span><span class="brand__dot"></span></div>

    <div class="story-panel">
      <svg width="222" height="300" viewBox="0 0 222 300" aria-hidden="true">
        <path d="M0 12 C60 0 120 18 222 4 L222 300 L0 300 Z" fill="var(--dark-panel)"/>
      </svg>
      <p class="story"><span class="story__initial">L</span>orem ipsum dolor sit amet, siala conadipisicing elit, sed do nulla in eiusmod tempor incididunt ut labore et dolore magna aliqua. Ut enim ad minim veniam, quis nostrud exercitation ullamco laboris nisi ut aliquip ex ea commodo consequat. Duis aute irure dolor in reprehenderit in voluptate velit esse cillum dolore eu fugiat nulla pariatur. Excepteur sint occaecat cupidatat non proident, sunt in culpa qui officia deserunt mollit de aboriable seool animidest laborum prehenderit in voluptate velit esse cillum dolore eu fugiat nulla pariatur cillum dolore eu fugiat nulla pariatur cillum dolore.</p>
      <span class="weight">30g</span>
    </div>

    <div class="year-badge" style="background: var(--dark-panel); box-shadow: 0 0 0 1px var(--dark-panel);">1989</div>
    <h2 class="flavour">PLAIN DARK<br>CHOCOLATE</h2>
    <div class="product-photo product-photo--dark" role="img" aria-label="Photo of broken dark chocolate pieces with cocoa powder"></div>
  </section>

</main>
</body>
</html>
```